professional business card design

Business card design. Photos have been uploaded and i am open to the designer choosing which photos to use. Would like the card to be mostyly in a grey scale design with black, whites, silver & grey colours. I have added copy of our flyer as would like on the back side of card our services to be listed. Do not use any bright colurs such as blue red green or yellow. i need to be able to edit the phone number and naem in the final card design submitted.

Target Market(s)

Clients

Industry/Entity Type

earhmovibng and transport

Contact Information for Business Card

Director Name, address, email, phone number and services

Colors

Designer to choose only greyscale colors for use in the design.

Requirements
Should not have
• no yellow, red, blue or green

```html
<!DOCTYPE html>
<html lang="en">
<head>
<meta charset="utf-8">
<title>Hale Haulage – Business Card</title>
<link rel="stylesheet" href="https://fonts.googleapis.com/css2?family=Archivo+Black&family=Arimo:ital,wght@0,400;0,700;1,400&display=swap">
<style>
  :root {
    --backdrop: #c9c9c9;
    --ink: #0a0a0a;
    --ink-soft: #1c1c1c;
    --white: #ffffff;
    --silver-light: #f2f2f2;
    --silver-mid: #c4c4c4;
    --silver-dark: #8e8e8e;
    --logo-silver: #d9d9d9;
    --dirt: #8a5a35;
    --dirt-light: #b07a4c;
    --truck: #2b2f2c;
  }
  * { box-sizing: border-box; margin: 0; padding: 0; }
  html, body { width: 1200px; height: 800px; overflow: hidden; }
  body {
    background: var(--backdrop);
    font-family: "Arimo", Arial, sans-serif;
    display: flex;
    align-items: center;
    justify-content: center;
    gap: 40px;
  }
  .card {
    position: relative;
    width: 560px;
    height: 320px;
    background: var(--ink);
    overflow: hidden;
    box-shadow: 0 10px 26px rgba(0,0,0,.28);
  }
  .mesh {
    position: absolute;
    left: 0; top: 0;
    background: radial-gradient(ellipse at 30% 40%, #3a3a3a 0%, #151515 55%, #050505 100%);
  }
  .truck-photo {
    position: absolute;
    background:
      linear-gradient(180deg, rgba(0,0,0,0) 60%, var(--dirt) 78%, var(--dirt-light) 100%),
      linear-gradient(90deg, #0b0b0b 0%, var(--truck) 40%, #3c403c 70%, #1a1a1a 100%);
  }
  .brushed {
    position: absolute;
    left: 0; width: 100%;
    background:
      repeating-linear-gradient(90deg, rgba(255,255,255,.18) 0 1px, rgba(0,0,0,.04) 1px 3px),
      linear-gradient(90deg, var(--silver-dark) 0%, var(--silver-light) 35%, var(--silver-mid) 65%, var(--silver-light) 100%);
  }
  .brand-name {
    position: absolute;
    font-family: "Archivo Black", Arial, sans-serif;
    color: var(--logo-silver);
    letter-spacing: 2px;
    line-height: 1;
    white-space: nowrap;
  }

  /* front */
  .front .mesh { width: 100%; height: 180px; }
  .front .truck-photo { right: 0; top: 0; width: 330px; height: 180px; }
  .front .brand-name { left: 28px; top: 48px; font-size: 44px; }
  .front .brand-name small { display: block; font-size: 17px; letter-spacing: 6px; margin-top: 6px; }
  .front .stripe { top: 176px; height: 6px; }
  .info-band {
    position: absolute;
    left: 0; top: 182px; width: 100%; height: 92px;
    background: var(--ink);
    color: var(--white);
    padding: 10px 26px 0;
  }
  .phone-line {
    display: flex; align-items: center; gap: 10px;
    font-family: "Archivo Black", Arial, sans-serif;
    font-size: 28px; letter-spacing: 1px;
  }
  .phone-line svg { width: 24px; height: 24px; }
  .contact-row { display: flex; align-items: center; margin-top: 8px; }
  .person .name { font-family: "Archivo Black", Arial, sans-serif; font-size: 19px; letter-spacing: .5px; }
  .person .role { font-size: 13px; margin-top: 1px; }
  .divider { width: 1px; height: 36px; background: var(--silver-dark); margin: 0 20px; }
  .links { font-size: 13px; line-height: 1.5; }
  .links div { display: flex; align-items: center; gap: 7px; }
  .links svg { width: 13px; height: 13px; }
  .front .address-band { top: 274px; height: 46px; display: flex; align-items: center; padding-left: 26px; }
  .address { font-size: 15px; color: var(--ink-soft); }

  /* back */
  .back .mesh { width: 100%; height: 172px; }
  .back .truck-photo { left: 0; top: 92px; width: 100%; height: 80px; }
  .back .brand-name { left: 0; width: 100%; text-align: center; top: 30px; font-size: 40px; }
  .back .heading-band { top: 164px; height: 38px; display: flex; align-items: center; justify-content: center; }
  .services-title { font-family: "Archivo Black", Arial, sans-serif; font-size: 25px; letter-spacing: 2px; color: var(--ink); }
  .services {
    position: absolute; left: 0; top: 202px; width: 100%; height: 76px;
    background: var(--ink); color: var(--white);
    text-align: center; font-size: 12.5px; line-height: 1.42; padding-top: 4px;
  }
  .back .cta-band { top: 278px; height: 42px; text-align: center; color: var(--ink); padding-top: 3px; }
  .cta-note { font-style: italic; font-size: 12px; }
  .cta-main { font-weight: 700; font-size: 15px; margin-top: 1px; }
</style>
</head>
<body>

  <section class="card front" aria-label="Business card front">
    <div class="mesh" role="img" aria-label="Dark metallic mesh background"></div>
    <div class="truck-photo" role="img" aria-label="Photo of a road train with tipper trailers on red outback dirt at dusk"></div>
    <div class="brand-name">HALE<small>HAULAGE</small></div>
    <div class="brushed stripe"></div>
    <div class="info-band">
      <div class="phone-line">
        <svg viewBox="0 0 24 24" aria-hidden="true"><path fill="#fff" d="M6.6 10.8a15.1 15.1 0 0 0 6.6 6.6l2.2-2.2a1 1 0 0 1 1-.25 11.4 11.4 0 0 0 3.6.57 1 1 0 0 1 1 1V20a1 1 0 0 1-1 1A17 17 0 0 1 3 4a1 1 0 0 1 1-1h3.5a1 1 0 0 1 1 1c0 1.25.2 2.45.57 3.6a1 1 0 0 1-.25 1z"/></svg>
        0498.555 273
      </div>
      <div class="contact-row">
        <div class="person">
          <div class="name">MARCUS HALE</div>
          <div class="role">Managing Director</div>
        </div>
        <div class="divider"></div>
        <div class="links">
          <div><svg viewBox="0 0 16 16" aria-hidden="true"><rect x="1" y="3" width="14" height="10" fill="none" stroke="#fff" stroke-width="1.4"/><path d="M1 3l7 6 7-6" fill="none" stroke="#fff" stroke-width="1.4"/></svg>info@halehaulage.com</div>
          <div><svg viewBox="0 0 16 16" aria-hidden="true"><circle cx="8" cy="8" r="6.5" fill="none" stroke="#fff" stroke-width="1.3"/><path d="M1.5 8h13M8 1.5c-3 3.5-3 9.5 0 13M8 1.5c3 3.5 3 9.5 0 13" fill="none" stroke="#fff" stroke-width="1.1"/></svg>www.halehaulage.com</div>
        </div>
      </div>
    </div>
    <div class="brushed address-band">
      <p class="address">18 Quarry Road, Redrock Flats, 60218</p>
    </div>
  </section>

  <section class="card back" aria-label="Business card back">
    <div class="mesh" role="img" aria-label="Dark metallic mesh background"></div>
    <div class="truck-photo" role="img" aria-label="Photo of a prime mover hauling three tipper trailers across red dirt"></div>
    <div class="brand-name">HALE HAULAGE</div>
    <div class="brushed heading-band">
      <h2 class="services-title">OUR SERVICES</h2>
    </div>
    <div class="services">
      <p>Over size loads/hot shot loads | Heavy vehicle recovery services</p>
      <p>Potable water deliveries | Road building/maintenance | Equipment &amp; operators</p>
      <p>Sand &amp; metal supply &amp; cartage | Road train tippers | Road train tankers</p>
      <p>Earthworks | Road train flat tops | Drop deck trailers | Mine site accredited</p>
    </div>
    <div class="brushed cta-band">
      <p class="cta-note">we offer a large range of services not listed.</p>
      <p class="cta-main">So call us today for a personalised quote to suit your needs.</p>
    </div>
  </section>

</body>
</html>
```